Redesign and move to Wordpress for corvandel.com

Our website needs a redesign and at the same time we are moving it to Wordpress. Please help us with a new digital professional look and feel.

We are an Australian Software Engineering company specialising in advanced software development using in A.I., PLatform Engineering, Integration and Cloud. See the current corvandel.com for more information about us.

```html
<!DOCTYPE html>
<html lang="en">
<head>
<meta charset="utf-8">
<title>Corvandel — Reliable Smart Software Engineering</title>
<link rel="stylesheet" href="https://fonts.googleapis.com/css2?family=Michroma&family=Barlow:wght@400;500;600;700&display=swap">
<style>
:root{
  --navy:#14456e;
  --blue:#1c5f9e;
  --teal:#3fb8b8;
  --teal-light:#5cc9c4;
  --ink:#1d1d1d;
  --muted:#666;
  --band:#f1f1f1;
  --footer:#2a2a2a;
  --white:#fff;
}
*{box-sizing:border-box;margin:0;padding:0}
html,body{width:1200px;height:3585px;overflow:hidden}
body{position:relative;font-family:"Barlow",sans-serif;color:var(--ink);background:var(--white)}
.abs{position:absolute}
.display{font-family:"Michroma",sans-serif;font-weight:400;letter-spacing:1px}

/* hero */
.hero{left:0;top:0;width:1200px;height:601px;overflow:hidden}
.hero-photo{position:absolute;inset:0;background:linear-gradient(100deg,#17506f 0%,#1f6a86 45%,#3a8ba1 65%,#1d4d66 100%)}
.hero-photo::after{content:"";position:absolute;left:560px;top:250px;width:360px;height:220px;border-radius:50%;background:radial-gradient(closest-side,rgba(140,230,255,.45),transparent)}
.brand{display:flex;align-items:center;gap:12px}
.brand-square{width:40px;height:40px;border:3px solid var(--teal)}
.brand-name{font-family:"Barlow",sans-serif;font-weight:500;font-size:32px;color:var(--white);letter-spacing:1px}
.nav{left:386px;top:36px;display:flex;gap:22px;align-items:center}
.nav a{color:var(--white);text-decoration:none;font-size:16px;letter-spacing:1px;font-weight:500}
.nav a.active{border:2px solid var(--teal);padding:3px 8px;color:var(--teal-light);font-weight:700}
.search{left:819px;top:26px;width:271px;height:50px;background:var(--white);border-radius:25px}
.search span{position:absolute;left:15px;top:15px;font-size:15px;color:#aaa}
.search-btn{position:absolute;right:2px;top:2px;width:46px;height:46px;border-radius:50%;background:var(--blue);display:flex;align-items:center;justify-content:center}
.hero-title{left:111px;top:176px;color:var(--white);font-size:41px;line-height:58px}
.btn-outline{display:inline-flex;align-items:center;justify-content:center;border:3px solid var(--blue);font-weight:700;font-size:17px;letter-spacing:.5px;text-decoration:none}
.hero-btn{left:114px;top:365px;width:160px;height:57px;color:var(--white);border-color:#2a7ab9}
.dots{left:570px;top:546px;display:flex;gap:9px}
.dots i{width:11px;height:11px;border-radius:50%;background:var(--white);display:block}
.dots i.on{background:var(--teal);box-shadow:0 0 0 2px #fff}

/* partners */
.teal-rule{left:0;top:601px;width:1200px;height:8px;background:var(--teal)}
.partners{left:0;top:609px;width:1200px;height:158px;background:var(--band);display:flex;justify-content:space-around;align-items:center;padding:0 90px}
.partner{font-family:"Barlow",sans-serif;font-weight:700;font-size:40px;color:#2f2f2f;display:flex;align-items:center;gap:10px}
.partner .sq{width:34px;height:34px;background:#2f2f2f}

/* section headings */
.section-title{left:0;width:1200px;text-align:center;font-size:34px}
.section-title .t{color:var(--teal)}
.section-title .b{color:var(--blue)}
.title-mark{width:30px;height:30px;border:3px solid var(--teal);left:585px}

/* services */
.svc{top:979px;width:234px;height:298px;background:var(--white);box-shadow:0 0 8px rgba(0,0,0,.08);text-align:center;padding-top:16px}
.svc.active{border:4px solid var(--teal);box-shadow:none;padding-top:12px}
.svc .icon{width:90px;height:90px;border-radius:50%;margin:0 auto;box-shadow:0 2px 6px rgba(0,0,0,.15);display:flex;align-items:center;justify-content:center}
.svc h3{font-size:17px;font-weight:600;letter-spacing:.5px;line-height:24px;margin-top:20px;height:48px}
.svc p{font-size:16px;color:var(--muted);line-height:22px;padding:0 12px;margin-top:12px;height:66px}
.svc .go{margin-top:10px}
.carousel-btn{top:1117px;width:40px;height:40px;border-radius:50%;background:linear-gradient(135deg,var(--blue),var(--teal));display:flex;align-items:center;justify-content:center}

/* about */
.about{left:0;top:1371px;width:1200px;height:518px;overflow:hidden;background:linear-gradient(135deg,#4cbcbb 0%,#2d8aab 45%,#1b5b9a 100%)}
.about-photo{position:absolute;inset:0;background:linear-gradient(120deg,#1c6f73,#2d8f94 40%,#c9a07c 80%,#6a5141);clip-path:polygon(707px 0,1200px 0,1200px 518px,550px 518px)}
.about-title{left:111px;top:56px;color:var(--white);font-size:33px}
.about-mark{left:111px;top:102px;width:32px;height:32px;border:3px solid var(--white)}
.about-text{left:111px;top:166px;width:490px;color:var(--white);font-size:18px;line-height:28px}
.about-text p+p{margin-top:8px}
.about-btn{left:112px;top:393px;width:145px;height:58px;color:var(--white);border-color:var(--white)}

/* news */
.news{overflow:hidden;border:11px solid var(--blue)}
.news.teal{border-color:var(--teal)}
.news .photo{position:absolute;inset:0}
.news .cap{position:absolute;left:19px;right:40px;bottom:18px;color:var(--white)}
.news h4{font-size:21px;font-weight:700;letter-spacing:.5px}
.news a{display:block;color:#63d3d0;font-size:16px;line-height:22px;margin-top:6px}
.news p{font-size:16px;line-height:24px;margin-top:4px}
.corner{position:absolute;right:8px;bottom:8px;width:36px;height:36px;border-radius:12px 0 0 0;background:var(--white);display:flex;align-items:center;justify-content:center}
.view-more{left:519px;top:2844px;width:160px;height:58px;color:var(--navy);border-color:var(--blue)}
.view-more{border-image:linear-gradient(90deg,var(--blue),var(--teal)) 1}

/* cta */
.cta{left:0;top:2994px;width:1200px;height:188px;background:linear-gradient(100deg,#41b6b6 0%,#2e8fb0 45%,#1c5c9d 100%)}
.cta h2{position:absolute;left:111px;top:52px;color:var(--white);font-size:31px;font-weight:600;line-height:39px;letter-spacing:.5px}
.cta .sub{position:absolute;left:111px;top:130px;color:var(--white);font-size:17px;font-weight:600}
.cta-btn{left:781px;top:65px;width:281px;height:64px;color:var(--white);border-color:var(--white);font-size:17px}

/* footer */
.footer{left:0;top:3182px;width:1200px;height:403px;background:var(--footer);color:var(--white)}
.footer h5{font-size:19px;font-weight:600;letter-spacing:.5px}
.f-links{position:absolute;left:349px;top:82px}
.f-links li{list-style:none;font-size:16px;margin-top:18px}
.f-links li.active{color:var(--teal);font-weight:700}
.social{position:absolute;top:160px;width:46px;height:46px;border-radius:50%;border:2px solid #ddd}
.social.on{background:#2a7ab9;border-color:#2a7ab9}
.contact{position:absolute;left:507px;top:82px}
.c-item{display:flex;gap:14px;margin-top:22px}
.c-item b{display:block;font-size:16px}
.c-item span{font-size:17px;line-height:22px}
.news-sub{position:absolute;left:780px;top:82px;width:340px}
.email{margin-top:28px;width:270px;height:50px;background:var(--white);border-radius:25px;position:relative}
.email span{position:absolute;left:15px;top:15px;color:#aaa;font-size:15px}
.email .send{position:absolute;right:2px;top:2px;width:46px;height:46px;border-radius:50%;background:#2a7ab9;display:flex;align-items:center;justify-content:center}
.news-sub .lead{margin-top:12px;font-size:15px;font-weight:700}
.news-sub em{display:block;font-size:15px}
.news-sub small{display:block;font-size:13px;margin-top:6px}
.f-rule{position:absolute;left:111px;top:351px;width:978px;height:1px;background:#555}
.copy{position:absolute;left:0;width:1200px;top:366px;text-align:center;font-size:16px}
</style>
</head>
<body>

<!-- HERO -->
<section class="abs hero">
  <div class="hero-photo" role="img" aria-label="Hands typing on a laptop with glowing AI symbol and floating chat bubbles"></div>
  <div class="abs brand" style="left:111px;top:28px"><span class="brand-square"></span><span class="brand-name">corvandel</span></div>
  <nav class="abs nav"><a class="active" href="#">HOME</a><a href="#">ABOUT</a><a href="#">SERVICES</a><a href="#">BLOG</a><a href="#">CONTACT</a></nav>
  <div class="abs search"><span>Search</span><div class="search-btn"><svg width="18" height="18" viewBox="0 0 18 18"><circle cx="7.5" cy="7.5" r="5.5" fill="none" stroke="#fff" stroke-width="2.5"/><line x1="11.5" y1="11.5" x2="16" y2="16" stroke="#fff" stroke-width="2.5"/></svg></div></div>
  <h1 class="abs display hero-title">RELIABLE SMART<br>SOFTWARE<br>ENGINEERING</h1>
  <a class="abs btn-outline hero-btn" href="#">GET STARTED</a>
  <div class="abs dots"><i></i><i class="on"></i><i></i></div>
</section>

<div class="abs teal-rule"></div>
<section class="abs partners">
  <div class="partner">Marlo</div>
  <div class="partner"><span class="sq"></span>Kestrane</div>
  <div class="partner">Trevik</div>
  <div class="partner">Brightfund</div>
</section>

<!-- SERVICES -->
<h2 class="abs display section-title" style="top:852px"><span class="t">OUR</span> <span class="b">SERVICES</span></h2>
<div class="abs title-mark" style="top:902px"></div>

<div class="abs carousel-btn" style="left:48px"><svg width="12" height="14" viewBox="0 0 12 14"><path d="M8 2 3 7l5 5" fill="none" stroke="#fff" stroke-width="2"/></svg></div>
<div class="abs carousel-btn" style="left:1110px"><svg width="12" height="14" viewBox="0 0 12 14"><path d="M4 2l5 5-5 5" fill="none" stroke="#fff" stroke-width="2"/></svg></div>

<article class="abs svc" style="left:114px">
  <div class="icon"><svg width="50" height="50" viewBox="0 0 50 50" fill="none" stroke="#333" stroke-width="2"><circle cx="25" cy="25" r="10"/><circle cx="25" cy="25" r="4"/><path d="M25 9v6M25 35v6M9 25h6M35 25h6M14 14l4 4M32 32l4 4M36 14l-4 4M14 36l4-4"/></svg></div>
  <h3>ENTERPRISE SYSTEMS<br>INTEGRATION</h3>
  <p>Automate your business pro-cesses internallyor externally to improve data</p>
  <svg class="go" width="22" height="16" viewBox="0 0 22 16"><path d="M2 8h17M13 2l6 6-6 6" fill="none" stroke="#2a7ab9" stroke-width="2.5"/></svg>
</article>
<article class="abs svc" style="left:359px">
  <div class="icon"><svg width="50" height="50" viewBox="0 0 50 50" fill="none" stroke="#333" stroke-width="2"><circle cx="25" cy="25" r="8"/><circle cx="25" cy="6" r="3"/><circle cx="25" cy="44" r="3"/><circle cx="7" cy="16" r="3"/><circle cx="43" cy="16" r="3"/><circle cx="7" cy="34" r="3"/><circle cx="43" cy="34" r="3"/><path d="M25 9v8M25 33v8M10 18l8 4M40 18l-8 4M10 32l8-4M40 32l-8-4"/></svg></div>
  <h3>MICRO<br>SERVICES</h3>
  <p>Leverage Microservices Architecture to enable quick deployment</p>
  <svg class="go" width="22" height="16" viewBox="0 0 22 16"><path d="M2 8h17M13 2l6 6-6 6" fill="none" stroke="#2a7ab9" stroke-width="2.5"/></svg>
</article>
<article class="abs svc active" style="left:607px">
  <div class="icon"><svg width="50" height="50" viewBox="0 0 50 50" fill="none" stroke="#1c5f9e" stroke-width="2"><rect x="8" y="10" width="34" height="24" rx="2"/><path d="M18 40h14M25 34v6M14 18h8M14 24h14M30 18h6"/></svg></div>
  <h3>PLATFORM<br>ENGINEERING</h3>
  <p>For organisations looking to manage the security and cost risks around their cloud</p>
  <svg class="go" width="22" height="16" viewBox="0 0 22 16"><path d="M2 8h17M13 2l6 6-6 6" fill="none" stroke="#2a7ab9" stroke-width="2.5"/></svg>
</article>
<article class="abs svc" style="left:852px">
  <div class="icon"><svg width="50" height="50" viewBox="0 0 50 50" fill="none" stroke="#333" stroke-width="2"><rect x="14" y="14" width="22" height="22"/><path d="M19 14V8M25 14V8M31 14V8M19 36v6M25 36v6M31 36v6M14 19H8M14 25H8M14 31H8M36 19h6M36 25h6M36 31h6"/><text x="25" y="30" font-size="11" font-family="Barlow" text-anchor="middle" fill="#333" stroke="none">AI</text></svg></div>
  <h3>CONVERSATIONAL<br>AI</h3>
  <p>Enabling legacy systems with conversational user interfaces, or simply building</p>
  <svg class="go" width="22" height="16" viewBox="0 0 22 16"><path d="M2 8h17M13 2l6 6-6 6" fill="none" stroke="#2a7ab9" stroke-width="2.5"/></svg>
</article>

<!-- ABOUT -->
<section class="abs about">
  <div class="about-photo" role="img" aria-label="Hands typing on a laptop surrounded by holographic AI and data icons"></div>
  <h2 class="abs display about-title">ABOUT US</h2>
  <div class="abs about-mark"></div>
  <div class="abs about-text">
    <p>Since our inception in 2013, we have been on a mission to make complex custom enterprise integration accessible to any organization, regardless of industry, size, or location.</p>
    <p>At Corvandel, we craft bespoke software solutions that are not available on the market. By building organizations market -leading products, process automation, legacy system enablement, or advanced intelligent systems</p>
  </div>
  <a class="abs btn-outline about-btn" href="#">READ MORE</a>
</section>

<!-- NEWS -->
<h2 class="abs display section-title" style="top:1976px"><span class="t">OUR</span> <span class="b">NEWS &amp; ARTICLES</span></h2>
<div class="abs title-mark" style="top:2029px"></div>

<article class="abs news" style="left:110px;top:2112px;width:477px;height:260px">
  <div class="photo" role="img" aria-label="Developers working at computer screens in a dim office" style="background:linear-gradient(135deg,#1f3e5e,#3a6a8e 50%,#203a52)"></div>
  <div class="cap"><h4>INDUSTRY RESEARCH</h4></div>
  <div class="corner"><svg width="16" height="16" viewBox="0 0 16 16"><path d="M13 2v11H2" fill="none" stroke="#222" stroke-width="2.5"/></svg></div>
</article>
<article class="abs news teal" style="left:110px;top:2390px;width:477px;height:409px">
  <div class="photo" role="img" aria-label="Glowing AI chip with floating chat bubbles on a dark background" style="background:linear-gradient(160deg,#21465c,#1c3a4d 50%,#3b6a74)"></div>
  <div class="cap">
    <h4>AI IN SOFTWARE ENGINEERING</h4>
    <a href="#">10 unexpected ways to use CodePilot Assist</a>
    <p>(DevHarbor Blog) CodePilot Assist is widely known for its code generation feature. Learn how the AI assistant’s abilities can extend beyond just code generation.</p>
  </div>
  <div class="corner"><svg width="16" height="16" viewBox="0 0 16 16"><path d="M13 2v11H2" fill="none" stroke="#222" stroke-width="2.5"/></svg></div>
</article>
<article class="abs news" style="left:611px;top:2112px;width:476px;height:412px">
  <div class="photo" role="img" aria-label="Blue holographic AI data chart over a keyboard" style="background:linear-gradient(135deg,#2b5c80,#1c3f63 55%,#152c48)"></div>
  <div class="cap">
    <h4>ARTIFICIAL INTELLIGENCE</h4>
    <a href="#">Advancing transparency: Updates on responsible AI research</a>
    <p>(Northlake Labs) A surge of generative AI models in the past year has fueled much discussion about thecan</p>
  </div>
  <div class="corner"><svg width="16" height="16" viewBox="0 0 16 16"><path d="M13 2v11H2" fill="none" stroke="#222" stroke-width="2.5"/></svg></div>
</article>
<article class="abs news teal" style="left:611px;top:2540px;width:476px;height:259px">
  <div class="photo" role="img" aria-label="Programmer with headphones at code screens in a warmly lit room" style="background:linear-gradient(120deg,#3a3430,#1d2430 50%,#233a55)"></div>
  <div class="cap"><h4>CONVERSATIONAL INTERFACES</h4></div>
  <div class="corner"><svg width="16" height="16" viewBox="0 0 16 16"><path d="M13 2v11H2" fill="none" stroke="#222" stroke-width="2.5"/></svg></div>
</article>

<a class="abs btn-outline view-more" href="#">VIEW MORE</a>

<!-- CTA -->
<section class="abs cta">
  <h2>BOOK AN OBLIGATION FREE CONSULTATION<br>WITH OUR LEAD TECHNOLOGIST</h2>
  <div class="sub">- MEET WITH OUR CTO</div>
  <a class="abs btn-outline cta-btn" href="#">BOOK AN &nbsp;FREE CONSULTATION</a>
</section>

<!-- FOOTER -->
<footer class="abs footer">
  <div class="abs brand" style="left:111px;top:82px"><span class="brand-square" style="width:50px;height:50px"></span><span class="brand-name" style="font-size:26px">corvandel</span></div>
  <span class="social on" style="left:113px" aria-label="Social profile"></span>
  <span class="social" style="left:174px" aria-label="Social profile"></span>
  <span class="social" style="left:236px" aria-label="Social profile"></span>

  <div class="f-links">
    <h5>QUICK LINKS</h5>
    <ul><li class="active">HOME</li><li>ABOUT</li><li>SERVICES</li><li>BLOG</li><li>CONTACT</li></ul>
  </div>

  <div class="contact">
    <h5>CONTACT US</h5>
    <div class="c-item"><svg width="18" height="18" viewBox="0 0 18 18"><path d="M4 1l3 4-2 2c1 2 3 4 5 5l2-2 4 3-2 3C8 16 2 10 1 4z" fill="#fff"/></svg><div><b>PHONE NO:</b><span>+61 3 5550 0142</span></div></div>
    <div class="c-item"><svg width="18" height="14" viewBox="0 0 18 14"><rect width="18" height="14" fill="#fff"/><path d="M1 1l8 7 8-7" fill="none" stroke="#2a2a2a" stroke-width="1.5"/></svg><div><b>EMAIL:</b><span>info@corvandel.com</span></div></div>
    <div class="c-item"><svg width="16" height="22" viewBox="0 0 16 22"><path d="M8 0a8 8 0 0 0-8 8c0 6 8 14 8 14s8-8 8-14a8 8 0 0 0-8-8z" fill="#fff"/><circle cx="8" cy="8" r="3" fill="#2a2a2a"/></svg><div><b>LOCATION:</b><span>Suite 210, 48 Harlow Street<br>Melbourne, VIC , 3006</span></div></div>
  </div>

  <div class="news-sub">
    <h5>SUBSCRIBE TO OUR NEWSLETTER</h5>
    <div class="email"><span>Email</span><div class="send"><svg width="20" height="18" viewBox="0 0 20 18"><path d="M1 8 19 1l-4 16-5-6-3 4V10z" fill="#fff"/></svg></div></div>
    <div class="lead">Australia's Largest health charity implements</div>
    <em>Corvandel API Msg Bus</em>
    <small>Register to our newsletter to find out more.</small>
  </div>

  <div class="f-rule"></div>
  <div class="copy">Copyright © 2025 Corvandel &nbsp;| All Rights Reserved.Privacy Policy</div>
</footer>

</body>
</html>
```